Create a PPTX template for our business

We need a Powerpoint and Keynote template design for a new company called "Quorvell" We connect hotel guests to hotel employees through text messaging so guests can ask for what they need during their stay. The name "Quorvell" is derived from the word "Affinity" which is how we want our hotel customer's employees and their guests to feel about each other. The color palette chosen is meant to evoke feelings of "warmth" and "comfort," which is how most people feel when they have a strong affinity to each other. The "-ium" ending of Quorvell is intended to give a technological feel to our business since we use technology to connect people together.

A *.ai file is included which contains our logo.

```html
<!DOCTYPE html>
<html lang="en">
<head>
<meta charset="utf-8">
<title>Quorvell Presentation Template</title>
<link rel="stylesheet" href="https://fonts.googleapis.com/css2?family=PT+Sans:ital,wght@0,400;0,700;1,400;1,700&family=PT+Sans+Narrow:wght@700&display=swap">
<style>
  :root {
    --backdrop: #1d2121;
    --teal: #27a79d;
    --teal-dark: #137f78;
    --teal-deep: #0e6f68;
    --lime: #d8dd2c;
    --lime-dark: #a9ae14;
    --cream: #fbfad8;
    --sky: #e3f3fb;
    --ink: #1e3a3a;
    --white: #ffffff;
  }
  * { box-sizing: border-box; margin: 0; padding: 0; }
  html, body { width: 818px; height: 1200px; overflow: hidden; background: var(--backdrop); }
  body { position: relative; font-family: "PT Sans", sans-serif; }

  .slide { position: absolute; left: 33px; width: 754px; height: 568px; overflow: hidden; box-shadow: 0 4px 14px rgba(0,0,0,.6); }
  .slide--cover { top: 22px; }
  .slide--content { top: 602px; background: linear-gradient(180deg, #d4edf8 0%, var(--sky) 40%, #fafdfe 100%); }

  /* cover */
  .cover__header { position: absolute; left: 0; top: 0; width: 100%; height: 330px; background: linear-gradient(180deg, #2aafa4 0%, var(--teal) 55%, var(--teal-dark) 100%); }
  .cover__rule { position: absolute; left: 0; width: 100%; height: 6px; background: var(--lime); }
  .cover__rule--top { top: 330px; }
  .cover__body { position: absolute; left: 0; top: 336px; width: 100%; height: 176px; background: linear-gradient(180deg, var(--cream) 0%, #fdfdf0 60%, #f4fbfb 100%); }
  .cover__rule--bottom { top: 512px; height: 4px; }
  .cover__title { position: absolute; right: 44px; top: 124px; font-family: "PT Sans Narrow", sans-serif; font-weight: 700; font-size: 42px; color: var(--white); text-shadow: 0 1px 2px rgba(0,0,0,.2); }
  .cover__subtext { position: absolute; right: 44px; top: 184px; width: 440px; text-align: right; font-family: "PT Sans Narrow", sans-serif; font-weight: 400; font-size: 16px; line-height: 25px; color: var(--white); }
  .portrait { position: absolute; left: 22px; top: 196px; width: 274px; height: 274px; border-radius: 50%; background: var(--lime); padding: 10px; box-shadow: 0 2px 6px rgba(0,0,0,.25); }
  .portrait__ring { width: 100%; height: 100%; border-radius: 50%; background: var(--teal); padding: 4px; }
  .portrait__photo { width: 100%; height: 100%; border-radius: 50%; border: 3px solid var(--white); background: radial-gradient(circle at 50% 45%, #e7cbb2 0%, #c89a7c 35%, #55504c 70%, #2e3136 100%); }
  .brand { position: absolute; left: 420px; top: 404px; display: flex; align-items: center; gap: 14px; }
  .brand__dot { width: 26px; height: 26px; border-radius: 50%; background: var(--teal); }
  .brand__name { font-family: "PT Sans", sans-serif; font-weight: 400; font-size: 46px; color: #4a4a4a; letter-spacing: 1px; }

  /* footer bar */
  .footer { position: absolute; left: 0; bottom: 0; width: 100%; height: 52px; background: linear-gradient(180deg, #2cb1a6 0%, var(--teal-dark) 100%); border-top: 4px solid var(--lime); }
  .slide--cover .footer { border-top: none; }
  .footer__page { position: absolute; left: 20px; top: 9px; width: 37px; height: 35px; background: linear-gradient(180deg, #dde23a, var(--lime-dark)); border: 2px solid #eef07a; border-radius: 3px; color: var(--white); font-size: 19px; line-height: 31px; text-align: center; }
  .footer__text { position: absolute; left: 116px; top: 14px; font-style: italic; font-size: 17px; color: var(--white); }
  .slide--cover .footer__text { font-weight: 700; letter-spacing: 1px; }
  .slide--content .footer__text { left: 82px; top: 12px; }
  .btn { position: absolute; top: 8px; height: 36px; }
  .btn span { position: absolute; inset: 0; display: flex; align-items: center; justify-content: center; color: var(--white); font-size: 15px; text-shadow: 0 1px 1px rgba(0,0,0,.3); }

  /* content slide */
  .content__flag { position: absolute; left: 0; top: 17px; }
  .content__title { position: absolute; left: 35px; top: 14px; font-family: "PT Sans", sans-serif; font-weight: 700; font-size: 30px; color: var(--teal-deep); }
  .content__heading { position: absolute; left: 55px; top: 92px; font-weight: 700; font-size: 20px; color: var(--teal-deep); }
  .checklist { position: absolute; left: 56px; top: 130px; width: 620px; list-style: none; }
  .checklist li { position: relative; padding-left: 28px; font-size: 15px; line-height: 24.6px; color: var(--ink); }
  .checklist svg { position: absolute; left: 0; top: 4px; }
</style>
</head>
<body>

<section class="slide slide--cover">
  <div class="cover__header"></div>
  <div class="cover__rule cover__rule--top"></div>
  <div class="cover__body"></div>
  <div class="cover__rule cover__rule--bottom"></div>
  <h1 class="cover__title">Project Title Here</h1>
  <p class="cover__subtext">Subtext here Subtext here Subtext here Subtext here Subtext here Subtext here Subtext here Subtext here</p>
  <div class="portrait"><div class="portrait__ring"><div class="portrait__photo" role="img" aria-label="Portrait photo of the presenter"></div></div></div>
  <div class="brand"><span class="brand__dot"></span><span class="brand__name">QUORVELL</span></div>
  <footer class="footer">
    <div class="footer__page">01</div>
    <div class="footer__text">01/02/15</div>
    <div class="btn" style="left:674px;width:62px">
      <svg width="62" height="36" viewBox="0 0 62 36"><path d="M4 1H50L61 18L50 35H4Q1 35 1 32V4Q1 1 4 1Z" fill="#c7cc1c" stroke="#eef07a" stroke-width="1.5"/></svg>
      <span style="padding-right:8px">Start</span>
    </div>
  </footer>
</section>

<section class="slide slide--content">
  <svg class="content__flag" width="30" height="38" viewBox="0 0 30 38"><path d="M0 0H30V38H0L10 19Z" fill="#1f9088"/></svg>
  <h2 class="content__title">Slide Title Presentation</h2>
  <h3 class="content__heading">Calden Modern Real Estate</h3>
  <ul class="checklist">
    <li><svg width="18" height="17" viewBox="0 0 18 17"><rect x="1" y="3" width="12" height="12" fill="none" stroke="#1d4a4a" stroke-width="1.6"/><path d="M3 8L7 12L17 1" fill="none" stroke="#1d4a4a" stroke-width="2.4"/></svg>High volume local boutique real estate company</li>
    <li><svg width="18" height="17" viewBox="0 0 18 17"><rect x="1" y="3" width="12" height="12" fill="none" stroke="#1d4a4a" stroke-width="1.6"/><path d="M3 8L7 12L17 1" fill="none" stroke="#1d4a4a" stroke-width="2.4"/></svg>Specialize in selling homes throughout the San Francisco Bay Area</li>
    <li><svg width="18" height="17" viewBox="0 0 18 17"><rect x="1" y="3" width="12" height="12" fill="none" stroke="#1d4a4a" stroke-width="1.6"/><path d="M3 8L7 12L17 1" fill="none" stroke="#1d4a4a" stroke-width="2.4"/></svg>Focus on modern marketing techniques and thinking outside the box</li>
    <li><svg width="18" height="17" viewBox="0 0 18 17"><rect x="1" y="3" width="12" height="12" fill="none" stroke="#1d4a4a" stroke-width="1.6"/><path d="M3 8L7 12L17 1" fill="none" stroke="#1d4a4a" stroke-width="2.4"/></svg>“High Tech and High Touch” approach to real estate</li>
    <li><svg width="18" height="17" viewBox="0 0 18 17"><rect x="1" y="3" width="12" height="12" fill="none" stroke="#1d4a4a" stroke-width="1.6"/><path d="M3 8L7 12L17 1" fill="none" stroke="#1d4a4a" stroke-width="2.4"/></svg>Certified Green Business Everything is done and stored online. No File Cabinets in our offices!</li>
    <li><svg width="18" height="17" viewBox="0 0 18 17"><rect x="1" y="3" width="12" height="12" fill="none" stroke="#1d4a4a" stroke-width="1.6"/><path d="M3 8L7 12L17 1" fill="none" stroke="#1d4a4a" stroke-width="2.4"/></svg>Exceptional web presence far beyond other local real estate companies</li>
    <li><svg width="18" height="17" viewBox="0 0 18 17"><rect x="1" y="3" width="12" height="12" fill="none" stroke="#1d4a4a" stroke-width="1.6"/><path d="M3 8L7 12L17 1" fill="none" stroke="#1d4a4a" stroke-width="2.4"/></svg>Clean, streamline, and hip marketing materials</li>
    <li><svg width="18" height="17" viewBox="0 0 18 17"><rect x="1" y="3" width="12" height="12" fill="none" stroke="#1d4a4a" stroke-width="1.6"/><path d="M3 8L7 12L17 1" fill="none" stroke="#1d4a4a" stroke-width="2.4"/></svg>A company constantly looking into the latest real estate trends, tools, and technology to better assist their agents and clients sell homes in the modern world, all while embracing tried and true real estate values and practices as well</li>
    <li><svg width="18" height="17" viewBox="0 0 18 17"><rect x="1" y="3" width="12" height="12" fill="none" stroke="#1d4a4a" stroke-width="1.6"/><path d="M3 8L7 12L17 1" fill="none" stroke="#1d4a4a" stroke-width="2.4"/></svg>Leading authority for architectural homes and recognized world wide</li>
    <li><svg width="18" height="17" viewBox="0 0 18 17"><rect x="1" y="3" width="12" height="12" fill="none" stroke="#1d4a4a" stroke-width="1.6"/><path d="M3 8L7 12L17 1" fill="none" stroke="#1d4a4a" stroke-width="2.4"/></svg>Not Just Modern Homes! We focus on Modern Real Estate<br>Practices through and through.</li>
  </ul>
  <footer class="footer">
    <div class="footer__page">04</div>
    <div class="footer__text">Tagline/Slogan about Your Company</div>
    <div class="btn" style="left:600px;width:62px">
      <svg width="62" height="36" viewBox="0 0 62 36"><path d="M58 1H12L1 18L12 35H58Q61 35 61 32V4Q61 1 58 1Z" fill="#c7cc1c" stroke="#eef07a" stroke-width="1.5"/></svg>
      <span style="padding-left:8px">Back</span>
    </div>
    <div class="btn" style="left:674px;width:62px">
      <svg width="62" height="36" viewBox="0 0 62 36"><path d="M4 1H50L61 18L50 35H4Q1 35 1 32V4Q1 1 4 1Z" fill="#c7cc1c" stroke="#eef07a" stroke-width="1.5"/></svg>
      <span style="padding-right:8px">Next</span>
    </div>
  </footer>
</section>

</body>
</html>
```